Yard sign

Looking for a yard sign. <br/>Something simple, name, number. <br/>Large text, readable from 50 feet away. <br/><br/>18 x 24 inches.

Target Market(s)

Potential homeowners thinking about going solar.

Colors

Designer to choose colors to be used in the design.

Requirements
Must have
• "WE'VE GONE SOLAR!"
Nice to have
• We are a solar company, we would like a design that compliments the homeowners decision that they went solar and encourages others to do the same.

```html
<!DOCTYPE html>
<html lang="en">
<head>
<meta charset="utf-8">
<title>We've Gone Solar – Yard Sign</title>
<link href="https://fonts.googleapis.com/css2?family=Oswald:wght@700&family=Montserrat:wght@700&display=swap" rel="stylesheet">
<style>
  :root {
    --backdrop: #231f20;
    --sign-orange: #e35204;
    --sign-glow: #f9a90c;
    --panel-dark: #333333;
    --panel-light: #454545;
    --chevron-silver: #d8d8d8;
    --chevron-shade: #a9a9a9;
    --brand-orange: #f3720d;
    --brand-yellow: #fbb40f;
    --text-white: #ffffff;
    --headline-shadow: #4a1a05;
  }
  html, body {
    margin: 0;
    padding: 0;
    width: 1200px;
    height: 1200px;
    overflow: hidden;
    background: var(--backdrop);
  }
  .yard-sign {
    display: block;
    width: 1200px;
    height: 1200px;
  }
  .headline {
    font-family: "Oswald", "Arial Narrow", sans-serif;
    font-weight: 700;
    font-size: 176px;
    fill: var(--text-white);
  }
  .headline-shadow {
    font-family: "Oswald", "Arial Narrow", sans-serif;
    font-weight: 700;
    font-size: 176px;
    fill: var(--headline-shadow);
  }
  .brand-name {
    font-family: "Montserrat", Arial, sans-serif;
    font-weight: 700;
    font-size: 58px;
    fill: var(--brand-orange);
  }
  .phone-number {
    font-family: "Montserrat", Arial, sans-serif;
    font-weight: 700;
    font-size: 120px;
    fill: var(--text-white);
  }
  .contact-name {
    font-family: "Montserrat", Arial, sans-serif;
    font-weight: 700;
    font-size: 42px;
    fill: var(--text-white);
  }
</style>
</head>
<body>
<svg class="yard-sign" viewBox="0 0 1200 1200" xmlns="http://www.w3.org/2000/svg">
  <defs>
    <radialGradient id="header-glow" cx="860" cy="185" r="520" gradientUnits="userSpaceOnUse">
      <stop offset="0" stop-color="var(--sign-glow)"/>
      <stop offset="1" stop-color="var(--sign-orange)"/>
    </radialGradient>
    <radialGradient id="panel-light" cx="600" cy="560" r="600" gradientUnits="userSpaceOnUse">
      <stop offset="0" stop-color="var(--panel-light)"/>
      <stop offset="1" stop-color="var(--panel-dark)"/>
    </radialGradient>
    <linearGradient id="chevron-band" x1="0" x2="1" y1="0" y2="0">
      <stop offset="0" stop-color="var(--chevron-shade)"/>
      <stop offset="0.5" stop-color="var(--chevron-silver)"/>
      <stop offset="1" stop-color="var(--chevron-shade)"/>
    </linearGradient>
    <filter id="sign-drop" x="-10%" y="-10%" width="120%" height="130%">
      <feGaussianBlur stdDeviation="12"/>
    </filter>
  </defs>

  <!-- ground shadow -->
  <rect class="sign-shadow" x="110" y="975" width="980" height="30" fill="#000" opacity="0.75" filter="url(#sign-drop)"/>

  <!-- dark middle panel -->
  <rect class="logo-panel" x="48" y="163" width="1103" height="634" fill="url(#panel-light)"/>

  <!-- silver chevron band -->
  <polygon class="chevron-band" points="48,397 600,446 1151,397 1151,407 600,472 48,407" fill="url(#chevron-band)"/>

  <!-- orange header -->
  <polygon class="header-band" points="48,163 1151,163 1151,397 600,446 48,397" fill="url(#header-glow)"/>

  <text class="headline-shadow" x="604" y="369" text-anchor="middle" textLength="1003" lengthAdjust="spacingAndGlyphs">WE'VE GONE SOLAR!</text>
  <text class="headline" x="600" y="365" text-anchor="middle" textLength="1003" lengthAdjust="spacingAndGlyphs">WE'VE GONE SOLAR!</text>

  <!-- brand name -->
  <g class="brand">
    <circle cx="395" cy="646" r="60" fill="var(--brand-yellow)"/>
    <text class="brand-name" x="480" y="667">Empire Sun Energy</text>
  </g>

  <!-- contact bands -->
  <rect class="divider-line" x="48" y="797" width="1103" height="6" fill="var(--sign-orange)"/>
  <rect class="contact-band" x="48" y="810" width="1103" height="180" fill="var(--sign-orange)"/>

  <text class="phone-number" x="600" y="915" text-anchor="middle" textLength="776" lengthAdjust="spacingAndGlyphs">123 456 7890</text>

  <g class="contact-name-row">
    <polygon points="263,952 397,950 397,955 263,953" fill="var(--text-white)"/>
    <text class="contact-name" x="598" y="968" text-anchor="middle">JONATHAN DOE</text>
    <polygon points="802,950 936,952 936,953 802,955" fill="var(--text-white)"/>
  </g>
</svg>
</body>
</html>
```